Brindlewick Solutions Ltd

I'd like to create a company letterhead for the attached logo in word format.

I'd like to emphasis the icon in large translucent state from the left corner and ensure that the letterhead colouring matches the colour palette of the current logo with a contrast so it's clear to see. I've attached a copy of our sister company page on the app for reference.

```html
<!DOCTYPE html>
<html lang="en">
<head>
<meta charset="utf-8">
<title>Brindlewick Solutions Ltd — Letterhead</title>
<link href="https://fonts.googleapis.com/css2?family=Lato:wght@400;700&display=swap" rel="stylesheet">
<style>
  :root {
    --teal: #00b9a5;
    --teal-pale: #dff4f0;
    --teal-mist: #eef9f7;
    --ink: #454545;
    --paper: #ffffff;
    --backdrop: #8c8c8c;
  }
  * { margin: 0; padding: 0; box-sizing: border-box; }
  html, body {
    width: 1061px;
    height: 1200px;
    overflow: hidden;
    background: var(--backdrop);
    font-family: "Lato", sans-serif;
  }
  .letterhead {
    position: absolute;
    left: 120px;
    top: 20px;
    width: 820px;
    height: 1160px;
    background: var(--paper);
    overflow: hidden;
  }
  .sunburst {
    position: absolute;
    left: 0;
    top: 0;
    width: 820px;
    height: 840px;
    background:
      radial-gradient(ellipse 560px 700px at 120px 160px,
        rgba(222, 244, 240, 0.9) 0%,
        rgba(222, 244, 240, 0.55) 45%,
        rgba(255, 255, 255, 0) 100%);
  }
  .corner-disc {
    position: absolute;
    left: 0;
    top: 0;
    width: 330px;
    height: 380px;
  }
  .brand {
    position: absolute;
    left: 42px;
    top: 140px;
    width: 220px;
    text-align: center;
    color: var(--teal);
    font-weight: 400;
  }
  .brand-name {
    font-size: 36px;
    line-height: 1;
    letter-spacing: 0.3px;
  }
  .brand-sub {
    font-size: 10px;
    letter-spacing: 7px;
    margin-top: 6px;
    padding-left: 7px;
  }
  .contact {
    position: absolute;
    left: 537px;
    top: 66px;
    height: 130px;
    padding-left: 22px;
    border-left: 1px solid var(--teal);
    color: var(--ink);
    font-size: 13.5px;
    line-height: 18px;
    font-style: normal;
  }
  .contact-company { color: var(--teal); }
  .contact-address { margin-bottom: 8px; }
  .contact-line { display: flex; align-items: center; gap: 7px; }
  .contact-line svg { width: 12px; height: 12px; fill: var(--teal); flex: none; }
</style>
</head>
<body>
  <main class="letterhead">
    <div class="sunburst" role="img" aria-label="Soft teal sunburst rays radiating from the top-left corner"></div>

    <svg class="corner-disc" viewBox="0 0 330 380" aria-hidden="true">
      <circle cx="116" cy="169" r="206" fill="var(--teal-mist)" opacity="0.9"/>
      <circle cx="116" cy="169" r="165" fill="var(--teal-pale)" opacity="0.85"/>
    </svg>

    <div class="brand">
      <div class="brand-name">Brindlewick</div>
      <div class="brand-sub">SOLUTIONS LTD</div>
    </div>

    <address class="contact">
      <div class="contact-company">Brindlewick Solutions Ltd</div>
      <div class="contact-address">47 Alder Crest Lane<br>Hartwell, CT 06512</div>
      <div class="contact-line">
        <svg viewBox="0 0 12 12" aria-hidden="true"><path d="M2.5 0.8l2 2.3-1 1.3c.7 1.6 2 2.9 3.6 3.6l1.3-1 2.3 2-1.3 2C5 10.8 1.2 7 .8 2.3z"/></svg>
        <span>(555) 204-3817</span>
      </div>
      <div class="contact-line">
        <svg viewBox="0 0 12 12" aria-hidden="true"><path d="M3 0h6v3H3zM1 4h10v5H9V7H3v2H1zM3.5 8h5v4h-5z"/></svg>
        <span>(555) 204-3818</span>
      </div>
      <div class="contact-line">
        <svg viewBox="0 0 12 12" aria-hidden="true"><path d="M0 2h12v1L6 7 0 3zM0 4.5l6 4 6-4V10H0z"/></svg>
        <span>info@brindlewicksolutions.com</span>
      </div>
      <div class="contact-line">
        <svg viewBox="0 0 12 12" aria-hidden="true"><circle cx="6" cy="6" r="6"/><path d="M3 3.5c1.2.3 1.5 1.3 2.6 1.4.8 1-.6 1.6-.2 2.8L4.6 10C3 8.8 3.6 7.3 2.2 6.6 1.8 5.5 2.2 4.3 3 3.5zM7.8 2.2c.9.5 1.2 1.2 2.2 1.5-.1 1.2-1.4.8-1.8 1.6-.7-.3-1.2-1.3-.4-3.1z" fill="#fff"/></svg>
        <span>brindlewicksolutions.com</span>
      </div>
    </address>
  </main>
</body>
</html>
```